Maple Roster Business Card for recruitment company

We are looking for a Business Card Design that incorporates our personal details and our busines name and logo. We are a specialized search consultancy that recruit Property and Construction professionals.
We would like a business card that stands out and is appealing to the Construction and Property industry as well.

Target Market(s)

people in the construction and property industry

Contact Information for Business Card

Business Name and logo

Font styles to use
Serif

Colors
0094D4
00A9DD
6FCCEA
C7EBF8
E9F6FB

Requirements
Must have
• Business name and logo as well as contact details
Should not have
• No photos of us please

```html
<!DOCTYPE html>
<html lang="en">
<head>
<meta charset="utf-8">
<title>Maple Roster – Business Card</title>
<link href="https://fonts.googleapis.com/css2?family=Lato:wght@300;400;700&display=swap" rel="stylesheet">
<style>
  :root {
    --backdrop: #e4e4e4;
    --paper: #ffffff;
    --teal-deep: #00324a;
    --teal-mid: #00566a;
    --teal-light: #006b7d;
    --ink-name: #0b4660;
    --ink-body: #4a4a4a;
    --ink-dark: #1e1e1e;
    --rule: #8fa9b4;
  }
  * { box-sizing: border-box; margin: 0; padding: 0; }
  html, body {
    width: 1200px; height: 1200px; overflow: hidden;
    background: var(--backdrop);
    font-family: "Lato", Arial, sans-serif;
  }
  .canvas { position: relative; width: 1200px; height: 1200px; }

  .card {
    position: absolute; left: 262px; width: 686px; height: 392px;
    overflow: hidden;
  }
  .card--front { top: 165px; background: var(--paper); }
  .card--back {
    top: 653px;
    background: linear-gradient(30deg, var(--teal-deep) 0%, var(--teal-mid) 55%, var(--teal-light) 100%);
  }

  .brand-name {
    position: absolute; left: 0; right: 0;
    text-align: center; font-weight: 300;
    letter-spacing: 2px; line-height: 1; white-space: nowrap;
  }
  .card--front .brand-name { top: 92px; font-size: 66px; color: var(--ink-name); }
  .card--back .brand-name { top: 160px; font-size: 70px; color: #ffffff; }

  .identity {
    position: absolute; right: 357px; top: 210px; text-align: right;
  }
  .identity__name {
    font-weight: 700; font-size: 22px; color: var(--ink-name);
    letter-spacing: 0.3px; line-height: 1.1;
  }
  .identity__role { font-size: 15.5px; color: var(--ink-dark); margin-top: 4px; }
  .identity__address { font-size: 15.5px; color: var(--ink-body); margin-top: 9px; line-height: 1.28; }

  .divider {
    position: absolute; left: 342px; top: 212px; height: 92px;
    border-left: 1px dashed var(--rule);
  }

  .contacts { position: absolute; left: 354px; top: 207px; list-style: none; }
  .contacts li {
    display: flex; align-items: center; height: 19.5px;
    font-size: 15.5px; color: var(--ink-body);
  }
  .contacts svg { width: 13px; height: 13px; margin-right: 8px; fill: var(--ink-name); flex: none; }

  .band {
    position: absolute; left: 0; right: 0; bottom: 0; height: 15px;
    background: linear-gradient(90deg, var(--teal-deep), var(--teal-mid));
  }
</style>
</head>
<body>
<div class="canvas">

  <section class="card card--front">
    <div class="brand-name">MAPLE ROSTER</div>

    <div class="identity">
      <div class="identity__name">DANIEL BROOKS</div>
      <div class="identity__role">President</div>
      <div class="identity__address">4210 Cedar Ridge Road<br>Juneau, Alaska 34810</div>
    </div>

    <div class="divider"></div>

    <ul class="contacts">
      <li>
        <svg viewBox="0 0 16 16" aria-hidden="true"><path d="M3.5 1l2.6 3-1.4 1.8c.9 2 2.5 3.6 4.5 4.5L11 8.9l3 2.6-1.3 2.8C6.5 14.3 1.7 9.5 1 3.3z"/></svg>
        555-214-7730
      </li>
      <li>
        <svg viewBox="0 0 16 16" aria-hidden="true"><path d="M4 1h8v14H4zM5.5 2.5v9.5h5V2.5z"/></svg>
        555-631-2948
      </li>
      <li>
        <svg viewBox="0 0 16 16" aria-hidden="true"><path d="M4 1h8v4H4zM1 6h14v6h-2v3H3v-3H1zM4.5 10v3.5h7V10z"/></svg>
        555-408-1562
      </li>
      <li>
        <svg viewBox="0 0 16 16" aria-hidden="true"><path d="M1 3.5h14v9H1zM2.5 5v.3L8 9l5.5-3.7V5L8 8.6z"/></svg>
        daniel@mapleroster.com
      </li>
      <li>
        <svg viewBox="0 0 16 16" aria-hidden="true"><circle cx="8" cy="8" r="7"/><path d="M5 4.5c1.5.3 2 1.5 1.2 2.5-.8.8.2 1.8 1.3 1.5 1-.2 1 1.4.2 2.2-.6.6-.2 1.8.3 2.3" stroke="#fff" stroke-width="1.3" fill="none"/></svg>
        www.mapleroster.com
      </li>
    </ul>

    <div class="band"></div>
  </section>

  <section class="card card--back">
    <div class="brand-name">MAPLE ROSTER</div>
  </section>

</div>
</body>
</html>
```